NEW Wordpress Website Design for a Dynamic Long Term Healthcare Company in Hawaii

I would like a new website design for my current company, Marlow Health Collective, which has two different brands - Marlow Homecare and Marlow Senior Living. You can see the current website at www.marlowhealth-example.com. The website should be built using Wordpress Software and the Framewise theme. The website should have a local Hawaii island/tropical feel, but look professional for healthcare. I'm looking for something fresh, and want the designer to select colors, styles, etc.

In the Header, on all pages, I would like a menu that includes Home Care, Senior Living, Rates, and About Us.
Under each of the Header Menu Titles, I would like these drop downs included:
Home Care (drop down pages)- Nurse Aide Care, 24-Hour Home Care, Skilled Nursing, Lifestyle Aide, Hospice at Home, Bathing & Meal Service.
Senior Living (drop down pages) - Long-Term Stay, Short-Term Stay.
Rates (drop down page) - Rates.
About Us (drop down pages) - Our Mission, Ohana Talk, About Dana Marlow.

In the footer, on all pages, you should include the address: 248 Pueo Lane, Suite 310, Honolulu, HI 96817. Phone number: 808-555-0172
The footer should also include buttons for a page called Learn, Caregiver Jobs, and each of the service page links to include: Nurse Aide Care, 24-Hour Home Care, Skilled Nursing, Lifestyle Aide, Hospice at Home, Bathing & Meal Service.
Please don't take the current website and redesign a few aspects. I'm looking for a completely different look and feel.

Target Market(s)

40-80 year olds

Industry/Entity Type

Long Term Healthcare

Coding

Coded - Design and coding required

Requirements
Should not have
• Our existing website as a template. We are looking for a complete redesign. Thank you.

```html
<!DOCTYPE html>
<html lang="en">
<head>
<meta charset="utf-8">
<title>Marlow Health Collective — Mobile Website Design</title>
<link href="https://fonts.googleapis.com/css2?family=Lora:wght@600;700&family=Open+Sans:wght@400;600&display=swap" rel="stylesheet">
<style>
:root{
  --bg:#f6f7f8;
  --page:#ffffff;
  --ink:#2b3a46;
  --muted:#8a96a0;
  --brand:#2f6384;
  --brand-dark:#24506c;
  --line:#e4e8ec;
  --footer-text:#e8f0f5;
}
*{box-sizing:border-box;margin:0;padding:0}
html,body{width:1200px;height:534px;overflow:hidden;background:var(--bg)}
body{font-family:"Open Sans",sans-serif;color:var(--ink);position:relative}
.board{display:flex;gap:12px;padding:20px 26px;height:534px}
.screen{width:220px;height:494px;background:var(--page);border-radius:14px;overflow:hidden;box-shadow:0 4px 18px rgba(30,60,80,.08);display:flex;flex-direction:column}
.photo{border-radius:6px}
h2.title{font-family:"Lora",serif;font-weight:700;color:var(--brand-dark);font-size:13px;line-height:1.2;border-left:3px solid var(--brand);padding-left:7px;margin:3px 0 5px}
.eyebrow{color:var(--brand);font-size:8px;font-weight:600}
p.body{font-size:6.6px;line-height:1.5;color:#4b5964}
.btn{display:inline-block;background:var(--brand);color:#fff;font-size:7.5px;padding:5px 14px;border-radius:20px;margin-top:7px}
.pad{padding:12px 14px}

/* hero screen */
.topbar{background:var(--brand);color:#fff;font-size:6.5px;display:flex;justify-content:space-between;padding:5px 12px}
.header{display:flex;justify-content:space-between;align-items:center;padding:8px 12px}
.brandname{font-family:"Lora",serif;font-weight:700;color:var(--brand-dark);font-size:10px;display:flex;align-items:center;gap:5px}
.brandname .dot{width:9px;height:9px;border-radius:50%;background:var(--brand)}
.menu span{display:block;width:12px;height:1.5px;background:var(--brand);margin:2.5px 0}
.hero{flex:1;position:relative;background:linear-gradient(180deg,#4d6b4a 0%,#6f8a6a 45%,#5d6f7c 100%);color:#fff;text-align:center;display:flex;flex-direction:column;justify-content:center;padding:0 14px}
.hero h1{font-family:"Lora",serif;font-weight:700;font-size:15px;line-height:1.3;margin-bottom:8px}
.hero p{font-size:6.6px;line-height:1.5}
.hero .btn{align-self:center}

/* services */
.card{border:1px solid var(--line);border-radius:8px;padding:8px 10px;margin-bottom:7px;position:relative}
.card .num{position:absolute;top:6px;right:8px;font-size:6px;color:var(--muted);border:1px solid var(--line);border-radius:8px;padding:1px 5px}
.icon{width:24px;height:24px;border-radius:50%;background:var(--brand);display:flex;align-items:center;justify-content:center;margin-bottom:4px}
.card h3{font-family:"Lora",serif;font-size:11px;color:var(--brand-dark);margin-bottom:3px}
.card p{font-size:6.4px;color:var(--muted);line-height:1.45}
.card .arrow{margin-top:3px}

ul.ticks{list-style:none;margin-top:5px}
ul.ticks li{font-size:7px;display:flex;align-items:center;gap:5px;margin:3px 0}

/* testimonial + footer */
.quote{background:linear-gradient(160deg,#4a4536,#2f3431);color:#fff;padding:12px 14px;height:170px}
.quote h3{font-family:"Lora",serif;font-size:12px;margin-bottom:6px}
.quote p{font-size:6.4px;line-height:1.5;font-style:italic}
.quote .who{margin-top:6px;font-family:"Lora",serif;font-size:8px;text-align:right}
.footer{background:var(--brand);color:var(--footer-text);flex:1;padding:10px 14px}
.footer .brandname{color:#fff;font-size:9px;margin-bottom:5px}
.footer .brandname .dot{background:#fff}
.footer p{font-size:6.2px;line-height:1.5}
.footer h4{font-family:"Lora",serif;color:#fff;font-size:10px;margin:7px 0 3px}
.footer ul{list-style:none;columns:2;column-gap:6px}
.footer li{font-size:6.2px;margin:1.5px 0}
.footer li::before{content:"✓ ";}
.social{display:flex;gap:4px;margin-top:4px}
.social span{width:8px;height:8px;border-radius:50%;background:var(--footer-text);opacity:.8}
.copy{font-size:5.6px;border-top:1px solid rgba(255,255,255,.3);margin-top:7px;padding-top:4px;text-align:center}
</style>
</head>
<body>
<div class="board">

  <!-- Home -->
  <section class="screen">
    <div class="topbar"><span>Opening Hours: Mon–Sun 24/7</span><span>808-555-0172</span></div>
    <div class="header">
      <div class="brandname"><span class="dot"></span>Marlow</div>
      <div class="menu"><span></span><span></span><span></span></div>
    </div>
    <div class="hero" role="img" aria-label="Caregiver walking with a senior using a walker under tropical palms">
      <h1>Compassionate Senior Care With A Hawaiian Spirit</h1>
      <p>At Marlow Health Collective, We Offer Personalized Home Care And Senior Living Services, Blending Professional Healthcare With The Warmth And Spirit Of Hawaii To Ensure The Best For Your Loved Ones.</p>
      <span class="btn">Learn More</span>
    </div>
  </section>

  <!-- About -->
  <section class="screen pad">
    <div class="eyebrow">About Us</div>
    <h2 class="title">Our Mission</h2>
    <p class="body">At Marlow Health Collective, Our Mission Is To Provide Exceptional, Personalized Care To Our Clients And Their Families. With A Deep Respect For The Unique Culture Of Hawaii, We Deliver Professional, Compassionate Services That Allow Seniors To Age With Dignity And Grace.</p>
    <h2 class="title" style="margin-top:9px">About Dana Marlow</h2>
    <p class="body">Dana Marlow Founded Marlow Health Collective With A Vision To Create A Nurturing Environment Where Seniors And Their Families Could Find Peace Of Mind. Born And Raised In Hawaii, Dana Embodies The Spirit Of Aloha In Every Aspect Of The Company.</p>
    <span class="btn">Learn More About Our Mission</span>
    <div style="display:flex;gap:6px;margin-top:10px">
      <div class="photo" role="img" aria-label="Nurse in blue scrubs chatting with a smiling senior woman" style="flex:1.3;height:110px;background:linear-gradient(160deg,#c9d79a,#3f8fbf)"></div>
      <div class="photo" role="img" aria-label="Portrait of a smiling nurse with a stethoscope" style="flex:1;height:110px;background:linear-gradient(160deg,#e6dfd6,#b68c70)"></div>
    </div>
  </section>

  <!-- Home Care -->
  <section class="screen pad">
    <div class="eyebrow">Home Care</div>
    <h2 class="title">Personalized Home Care With Heart</h2>
    <p class="body">At Marlow Health Collective, Our Home Care Services Are Designed To Help Individuals Maintain Their Independence In The Comfort Of Their Own Homes. From Skilled Nursing To Lifestyle Assistance, We Create Customized Care Plans.</p>
    <div class="photo" role="img" aria-label="Caregiver assisting a senior man at home" style="height:92px;margin:8px 0;background:linear-gradient(160deg,#e9dca0,#3aa6c9 70%,#6b7c8c)"></div>
    <div class="card">
      <span class="num">Service 01</span>
      <div class="icon"><svg width="12" height="12" viewBox="0 0 12 12"><circle cx="6" cy="4" r="2.3" fill="none" stroke="#fff" stroke-width="1.2"/><path d="M2 11c0-2.5 2-4 4-4s4 1.5 4 4" fill="none" stroke="#fff" stroke-width="1.2"/></svg></div>
      <h3>Nurse Aide Care</h3>
      <p>Aides assist with daily tasks, mobility, and comfort.</p>
    </div>
    <div class="card">
      <span class="num">Service 03</span>
      <h3>Skilled Nursing</h3>
      <p>Licensed nurses provide medical care at home, from post-op to chronic condition management.</p>
      <svg class="arrow" width="14" height="6" viewBox="0 0 14 6"><path d="M0 3h13M10 .5L13 3l-3 2.5" fill="none" stroke="#8a96a0"/></svg>
    </div>
  </section>

  <!-- Services + Senior Living -->
  <section class="screen pad">
    <div class="card">
      <span class="num">Service 04</span>
      <div class="icon"><svg width="12" height="12" viewBox="0 0 12 12"><rect x="1.5" y="3.5" width="9" height="6" rx="1" fill="none" stroke="#fff" stroke-width="1.2"/><path d="M6 5v3M4.5 6.5h3" stroke="#fff" stroke-width="1.2"/></svg></div>
      <h3>Lifestyle Aide</h3>
      <p>Assistance with social activities, errands, and recreation to help seniors stay engaged and active.</p>
    </div>
    <div class="card">
      <span class="num">Service 05</span>
      <div class="icon"><svg width="12" height="12" viewBox="0 0 12 12"><path d="M6 10.5S1.5 7.5 1.5 4.5A2.2 2.2 0 0 1 6 3.5a2.2 2.2 0 0 1 4.5 1C10.5 7.5 6 10.5 6 10.5z" fill="none" stroke="#fff" stroke-width="1.2"/></svg></div>
      <h3>Hospice at Home</h3>
      <p>Compassionate end-of-life care, ensuring comfort and peace for patients and their families.</p>
    </div>
    <div class="card">
      <span class="num">Service 06</span>
      <h3>Bathing &amp; Meal Service</h3>
      <p>Personalized bathing assistance and meal preparation to promote hygiene and nutrition.</p>
    </div>
    <div class="eyebrow" style="margin-top:4px">Senior Living</div>
    <h2 class="title">Comfortable, Safe Senior Living In Paradise</h2>
    <p class="body">Marlow Senior Living Offers Both Long-Term And Short-Term Stays In A Warm, Supportive Environment Focused On Well-Being.</p>
    <ul class="ticks">
      <li><svg width="8" height="8" viewBox="0 0 8 8"><rect x=".5" y=".5" width="7" height="7" fill="none" stroke="#2f6384"/><path d="M2 4l1.5 1.5L6 2.5" fill="none" stroke="#2f6384"/></svg>Long-Term Stay</li>
      <li><svg width="8" height="8" viewBox="0 0 8 8"><rect x=".5" y=".5" width="7" height="7" fill="none" stroke="#2f6384"/><path d="M2 4l1.5 1.5L6 2.5" fill="none" stroke="#2f6384"/></svg>Short-Term Stay</li>
    </ul>
  </section>

  <!-- Testimonial + Footer -->
  <section class="screen">
    <div class="quote" role="img" aria-label="Senior residents knitting together in a sunny lounge, darkened behind a testimonial">
      <h3>What Our Families Say</h3>
      <p>“After my mom’s surgery, we needed a place where she could recover with the right level of support, but we also wanted to ensure she felt at home. Marlow Senior Living provided that perfect balance. The staff treated my mom with such dignity and respect, always checking in on her well-being and encouraging her to stay active.”</p>
      <div class="who">– Keoni R.</div>
    </div>
    <footer class="footer">
      <div class="brandname"><span class="dot"></span>Marlow Health Collective</div>
      <p>248 Pueo Lane, Suite 310, Honolulu, HI 96817<br><b>Phone:</b> 808-555-0172<br><b>Email:</b> info@marlowhealth-example.com</p>
      <div class="social"><span></span><span></span><span></span></div>
      <h4>Quick Links</h4>
      <ul>
        <li>Learn</li><li>Caregiver Jobs</li><li>Nurse Aide Care</li><li>24-Hour Home Care</li>
        <li>Skilled Nursing</li><li>Lifestyle Aide</li><li>Hospice at Home</li><li>Bathing &amp; Meal Service</li>
      </ul>
      <h4>Our Services</h4>
      <ul><li>Home Care Services</li><li>Senior Living Services</li></ul>
      <h4>Our Hospices</h4>
      <div role="img" aria-label="Map showing hospice locations" style="height:34px;border-radius:4px;background:linear-gradient(135deg,#cfe3f2,#e9eef0)"></div>
      <div class="copy">© 2024 Marlow Health Collective. All Rights Reserved. · About us | Contact | Services</div>
    </footer>
  </section>

</div>
</body>
</html>
```